Business card design for Quorvane Engineering Tandem

We need a new business card design along with all the necessary to place an order. The company is Quorvane Engineering Tandem and we recently updated our logo.

```html
<!DOCTYPE html>
<html lang="en">
<head>
<meta charset="utf-8">
<title>Quorvane Engineering Tandem – Business Card</title>
<link rel="stylesheet" href="https://fonts.googleapis.com/css2?family=Montserrat:wght@700&family=Nunito+Sans:wght@400;600&display=swap">
<style>
  :root {
    --backdrop: #2a2a2c;
    --card-white: #ffffff;
    --card-dark: #262626;
    --brand-grey: #9a9a9a;
    --brand-yellow: #e3bd22;
    --text-light: #c9c9c9;
  }
  * { margin: 0; padding: 0; box-sizing: border-box; }
  html, body { width: 1200px; height: 982px; overflow: hidden; }
  body {
    background: var(--backdrop);
    position: relative;
    font-family: "Nunito Sans", sans-serif;
  }
  .card {
    position: absolute;
    width: 620px;
    height: 354px;
    border-radius: 22px;
    box-shadow: 0 14px 30px rgba(0,0,0,.45);
  }
  .card-front {
    left: 470px; top: 90px;
    background: var(--card-white);
    display: flex; align-items: center; justify-content: center;
  }
  .card-back {
    left: 110px; top: 500px;
    background: var(--card-dark);
    padding: 34px 40px;
  }
  .wordmark {
    display: flex; align-items: center; gap: 14px;
    font-family: "Montserrat", sans-serif;
    font-weight: 700;
    color: var(--brand-grey);
    letter-spacing: .02em;
    white-space: nowrap;
  }
  .wordmark-mark {
    width: 18px; height: 18px;
    background: var(--brand-yellow);
    flex: none;
  }
  .card-front .wordmark { font-size: 31px; }
  .card-back .wordmark { font-size: 22px; gap: 10px; }
  .card-back .wordmark-mark { width: 12px; height: 12px; }
  .holder-name {
    margin-top: 26px;
    font-family: "Montserrat", sans-serif;
    font-weight: 700;
    font-size: 24px;
    color: var(--brand-grey);
    letter-spacing: .01em;
  }
  .holder-role {
    font-size: 17px;
    color: var(--brand-yellow);
    margin-top: 2px;
  }
  .contact-list {
    list-style: none;
    margin-top: 16px;
    font-size: 14.5px;
    color: var(--text-light);
    line-height: 1.55;
  }
  .contact-list li { display: flex; align-items: flex-start; gap: 10px; }
  .contact-list svg { width: 13px; height: 13px; margin-top: 4px; flex: none; fill: var(--brand-yellow); }
</style>
</head>
<body>
  <section class="card card-front" aria-label="Card front">
    <div class="wordmark"><span class="wordmark-mark"></span>Quorvane Engineering Tandem</div>
  </section>

  <section class="card card-back" aria-label="Card back">
    <div class="wordmark"><span class="wordmark-mark"></span>Quorvane Engineering Tandem</div>
    <h1 class="holder-name">DANIEL REYES</h1>
    <p class="holder-role">Founder &amp; CEO</p>
    <ul class="contact-list">
      <li><svg viewBox="0 0 12 12"><path d="M6 0a4 4 0 0 0-4 4c0 3 4 8 4 8s4-5 4-8a4 4 0 0 0-4-4zm0 5.5A1.5 1.5 0 1 1 6 2.5a1.5 1.5 0 0 1 0 3z"/></svg><span>423 Street Address Here, City<br>State, Country, ZIP Code</span></li>
      <li><svg viewBox="0 0 12 12"><path d="M2.5 0l2 3-1.2 1.3a7 7 0 0 0 4.4 4.4L9 7.5l3 2-1.2 2.2C5 12 0 7 .3 1.2z"/></svg><span>(123) 456-7890</span></li>
      <li><svg viewBox="0 0 12 12"><path d="M3 0h6v12H3zM4 1.5v8h4v-8z"/></svg><span>(123) 456-7890</span></li>
      <li><svg viewBox="0 0 12 12"><path d="M3 0h6v3H3zM1 4h10v5H9v3H3V9H1zm3 4v3h4V8z"/></svg><span>(123) 456-7890</span></li>
      <li><svg viewBox="0 0 12 12"><path d="M0 2h12v1L6 7 0 3zm0 2.5l6 4 6-4V10H0z"/></svg><span>info@yourwebsitehere.com</span></li>
      <li><svg viewBox="0 0 12 12"><circle cx="6" cy="6" r="6"/></svg><span>yourwebsitehere.com</span></li>
    </ul>
  </section>
</body>
</html>
```